Calloway needs a modernized design

We would like a modern update (that can be responsive) to our existing website. Attached are the two existing pages we would like new concepts of - our home page and a page about one of our locations.

Calloway is provides executive offices and virtual office services. Startups, law firms, and financial services are our primary clients. We would like a professional, clean design, leaning towards minimalist. We intend to greatly reduce/eliminate the long paragraphs of text.

Requirements
Must have
• A design that can be responsive
Nice to have
• Large image(s) on home page that rotate.

```html
<!DOCTYPE html>
<html lang="en">
<head>
<meta charset="utf-8">
<title>Calloway Business Centers</title>
<link href="https://fonts.googleapis.com/css2?family=Cinzel:wght@400;700&family=Lato:wght@400;700&display=swap" rel="stylesheet">
<style>
:root{
  --navy:#27366b;
  --navy-deep:#1f2d5c;
  --orange:#f7941d;
  --text:#555a63;
  --light:#f3f3f3;
  --mid:#e6e6e6;
  --white:#ffffff;
  --rule:#c9ccd4;
}
*{box-sizing:border-box;margin:0;padding:0}
html,body{width:1200px;height:2769px;overflow:hidden}
body{position:relative;background:var(--white);font-family:'Lato',Arial,sans-serif;color:var(--text)}
.abs{position:absolute}
.serif{font-family:'Cinzel',Georgia,serif}

/* header */
.site-header{left:0;top:0;width:1200px;height:110px;background:var(--white);border-top:3px solid var(--navy)}
.brand{left:60px;top:18px;display:flex;align-items:center;gap:12px}
.brand-dot{width:66px;height:66px;border-radius:50%;background:var(--navy)}
.brand-name{font-family:'Cinzel',Georgia,serif;font-weight:700;font-size:30px;color:var(--navy);line-height:1;width:220px}
.social-top{left:824px;top:8px;display:flex;gap:8px}
.social-top span{width:24px;height:24px;border-radius:50%}
.phone-tab{left:966px;top:0;width:210px;height:34px;background:var(--navy);border-radius:0 0 0 30px;color:var(--white);font-size:18px;display:flex;align-items:center;justify-content:center;gap:10px}
.main-nav{left:472px;top:62px;display:flex;align-items:center;gap:0}
.main-nav a{font-family:'Cinzel',Georgia,serif;font-size:15px;color:#222;text-decoration:none;padding:0 16px;border-left:1px solid #ccc;letter-spacing:.5px}
.main-nav a:first-of-type{border-left:none}
.main-nav svg{margin-right:10px}

/* hero */
.hero{left:0;top:110px;width:1200px;height:510px;background:linear-gradient(100deg,#c9d3de 0%,#e6ecf2 35%,#b8c4d2 60%,#dfe5ea 100%)}
.hero-caption{left:0;top:452px;width:1200px;height:58px;background:rgba(40,40,40,.78);color:var(--white);font-size:33px;text-align:center;line-height:58px;letter-spacing:.3px}
.hero-arrow{top:240px;width:20px;height:40px;background:var(--white);display:flex;align-items:center;justify-content:center}

/* section titles */
.sec-title{font-family:'Cinzel',Georgia,serif;color:var(--navy);font-size:36px;letter-spacing:1px;text-align:center;width:100%}
.divider{display:flex;align-items:center;justify-content:center;gap:10px}
.divider i{display:block;width:260px;height:1px;background:var(--rule)}
.divider b{display:block;width:22px;height:22px;border-radius:50%;background:var(--navy)}

.btn{display:inline-flex;align-items:center;gap:8px;height:30px;padding:0 16px 0 4px;border-radius:16px;font-size:14px;color:var(--white)}
.btn span.dot{width:24px;height:24px;border-radius:50%;background:var(--navy)}
.btn-orange{background:var(--orange)}
.btn-navy{background:var(--navy)}
.btn-orange-on-navy{background:var(--orange)}

/* welcome */
.welcome{left:0;top:620px;width:1200px;height:388px}
.welcome .sec-title{position:absolute;top:38px}
.welcome .divider{position:absolute;top:92px;width:100%}
.welcome-lead{position:absolute;top:134px;left:100px;width:1000px;text-align:center;color:var(--navy);font-weight:700;font-size:18px;line-height:1.45}
.welcome-body{position:absolute;top:202px;left:90px;width:1020px;text-align:center;font-size:14px;line-height:1.6}
.welcome .btn{position:absolute;top:300px;left:530px}

/* offers */
.offer{top:1008px;width:600px;height:465px;color:var(--white)}
.offer-left{left:0;background:linear-gradient(180deg,#2c3c73,#25336a)}
.offer-right{left:600px;background:linear-gradient(180deg,#f79a2a,#f28d17)}
.notch{left:580px;top:1008px;width:0;height:0;border-left:20px solid transparent;border-right:20px solid transparent;border-top:18px solid var(--white)}
.offer-icon{top:58px;width:130px;height:130px;border-radius:50%;display:flex;align-items:center;justify-content:center}
.offer-left .offer-icon{left:242px;background:var(--orange)}
.offer-right .offer-icon{left:242px;background:var(--navy)}
.icon-fill{width:60px;height:64px;border-radius:8px;background:rgba(255,255,255,.85)}
.offer h2{position:absolute;top:200px;width:100%;text-align:center;font-family:'Cinzel',Georgia,serif;font-weight:400;font-size:33px;letter-spacing:1px}
.offer-left h2{color:var(--orange)}
.offer ul{position:absolute;top:266px;left:106px;width:420px;list-style:none;display:grid;grid-template-columns:160px 230px;row-gap:12px;font-size:14px;font-weight:700}
.offer-right ul{left:104px;grid-template-columns:240px 170px}
.offer li{display:flex;align-items:center;gap:8px}
.offer .btn{position:absolute;top:377px;left:238px}
.offer-right .btn{left:232px}
.link-line{left:382px;top:1130px;width:436px;height:2px;background:rgba(255,255,255,.55)}
.center-seal{left:560px;top:1088px;width:80px;height:80px;border-radius:50%;background:var(--white);border:4px solid var(--navy)}

/* community + services */
.community{left:0;top:1473px;width:596px;height:552px;background:var(--mid)}
.services{left:596px;top:1473px;width:604px;height:552px;background:var(--light)}
.block-title{font-family:'Cinzel',Georgia,serif;color:var(--navy);font-size:33px;letter-spacing:1px}
.community .block-title{position:absolute;left:62px;top:42px}
.community-photo{position:absolute;left:62px;top:130px;width:490px;height:200px;background:linear-gradient(135deg,#8a5a3b,#c79470 45%,#6d4a35)}
.community p{position:absolute;left:62px;top:348px;width:494px;font-size:13.5px;line-height:1.62;color:#333}
.read-link{font-size:14px;color:var(--navy);font-weight:700}
.community .read-link{position:absolute;left:62px;top:482px}
.services .block-title{position:absolute;left:45px;top:42px}
.services .rule-top{position:absolute;left:45px;top:98px;width:510px;height:1px;background:#d5d5d5}
.svc{position:absolute;left:45px;width:510px;height:136px;border-bottom:1px dashed #9aa0ad}
.svc-icon{position:absolute;left:0;top:12px;width:62px;height:62px;border-radius:50%;background:#333}
.svc h3{position:absolute;left:78px;top:10px;font-size:20px;color:var(--orange);font-weight:700}
.svc p{position:absolute;left:78px;top:42px;width:430px;font-size:13.5px;line-height:1.55;color:#333}
.svc .read-link{position:absolute;left:78px;top:92px}

/* partners */
.partners{left:0;top:2025px;width:1200px;height:335px}
.partners .sec-title{position:absolute;top:50px}
.partners .divider{position:absolute;top:104px;width:100%}
.partner-row{position:absolute;left:60px;top:170px;display:flex;gap:28px}
.partner{width:156px;height:74px;border:1px solid #cfd2d8;background:var(--white);display:flex;align-items:center;justify-content:center}
.partner span{width:90px;height:26px;border-radius:4px;background:#9a9ea6}
.p-arrow{top:195px}

/* footer */
.footer-curve{left:0;top:2360px}
.footer-seal{left:558px;top:2312px;width:84px;height:84px;border-radius:50%;background:var(--white);border:5px solid var(--navy)}
.footer{left:0;top:2420px;width:1200px;height:302px;background:var(--navy-deep);color:var(--white)}
.f-col{position:absolute;top:42px}
.f-col h4{font-family:'Cinzel',Georgia,serif;font-weight:400;font-size:20px;letter-spacing:1px;margin-bottom:14px;padding-bottom:14px;border-bottom:1px solid rgba(255,255,255,.25)}
.f-links{list-style:none;font-size:13.5px}
.f-links li{margin-bottom:19px;display:flex;align-items:center;gap:12px}
.f-links li::before{content:"";width:5px;height:5px;border-radius:50%;background:var(--orange)}
.contact-row{display:flex;gap:12px;font-size:13.5px;margin-bottom:18px;line-height:1.5}
.contact-row svg{flex:none;margin-top:3px}
.field{width:276px;height:36px;background:var(--white);border-radius:2px;margin-bottom:8px;color:#777;font-size:13.5px;padding:9px 10px}
.submit{width:128px;height:36px;background:#3f5aa8;color:var(--white);font-weight:700;font-size:15px;display:flex;align-items:center;justify-content:center}
.follow li{list-style:none;display:flex;align-items:center;gap:14px;font-size:13.5px;margin-bottom:14px}
.follow li span{width:32px;height:32px;border-radius:50%}
.v-rule{top:2462px;width:1px;height:232px;background:rgba(255,255,255,.15)}
.copyright{left:0;top:2722px;width:1200px;height:47px;background:var(--orange);color:var(--white);font-size:13.5px;font-weight:700;text-align:center;line-height:47px}
</style>
</head>
<body>

<header class="site-header abs">
  <div class="brand abs"><span class="brand-dot"></span><span class="brand-name">CALLOWAY BUSINESS CENTERS</span></div>
  <div class="social-top abs"><span style="background:#d2232a"></span><span style="background:#0e76a8"></span><span style="background:#1da1f2"></span><span style="background:#dd4b39"></span></div>
  <div class="phone-tab abs">
    <svg width="18" height="18" viewBox="0 0 24 24"><circle cx="12" cy="12" r="11" fill="none" stroke="#fff" stroke-width="2"/><path d="M8 6l2 0 1 3-1.5 1a7 7 0 0 0 3.5 3.5l1-1.5 3 1 0 2a2 2 0 0 1-2 2A9 9 0 0 1 6 8a2 2 0 0 1 2-2z" fill="#fff"/></svg>
    + 214.555.0148
  </div>
  <nav class="main-nav abs">
    <svg width="26" height="26" viewBox="0 0 24 24"><path d="M2 12L12 3l10 9h-3v9h-5v-6h-4v6H5v-9z" fill="#27366b"/></svg>
    <a>Properties</a><a>Virtual Tours &amp; Videos</a><a>Photos</a><a>Broker Referrals</a>
  </nav>
</header>

<section class="hero abs" role="img" aria-label="Rotating photo of business people in a meeting around a laptop">
  <div class="hero-arrow abs" style="left:0;border-radius:0 4px 4px 0"><svg width="10" height="14" viewBox="0 0 10 14"><path d="M8 1L2 7l6 6" stroke="#222" stroke-width="2" fill="none"/></svg></div>
  <div class="hero-arrow abs" style="left:1180px;border-radius:4px 0 0 4px"><svg width="10" height="14" viewBox="0 0 10 14"><path d="M2 1l6 6-6 6" stroke="#222" stroke-width="2" fill="none"/></svg></div>
  <div class="hero-caption abs">We Provide Executive Offices And Virtual Office Services</div>
</section>

<section class="welcome abs">
  <h1 class="sec-title" style="font-weight:400">WELCOME TO CALLOWAY BUSINESS CENTERS</h1>
  <div class="divider"><i></i><b></b><i></i></div>
  <p class="welcome-lead">Come See Why Smarter Companies are Choosing Calloway Business Centers' Dallas, Ft. Worth and Houston Executive Office Suites, Virtual Offices, Meeting Rooms and Video Conferencing.</p>
  <p class="welcome-body">Either you need Dallas/Ft. Worth Office Space, Dallas Executive Suites, Ft. Worth Executive Suites, Houston Office Space, Houston Executive Suites, or maybe you simply need a place to stop in and use an on-demand office or meeting room from time to time or utilize our local business phone numbers, phone answering or business addresses through one of our virtual office solutions</p>
  <span class="btn btn-orange"><span class="dot"></span>Read More »</span>
</section>

<section class="offer offer-left abs">
  <div class="offer-icon abs"><div class="icon-fill" role="img" aria-label="Office chair icon"></div></div>
  <h2>EXECUTIVE OFFICES</h2>
  <ul>
    <li><svg width="12" height="12" viewBox="0 0 12 12"><path d="M1 6l3 3 7-7" stroke="#f7941d" stroke-width="2.4" fill="none"/></svg>Full Service Offices</li>
    <li><svg width="12" height="12" viewBox="0 0 12 12"><path d="M1 6l3 3 7-7" stroke="#f7941d" stroke-width="2.4" fill="none"/></svg>Flexible Contracts from $395</li>
    <li><svg width="12" height="12" viewBox="0 0 12 12"><path d="M1 6l3 3 7-7" stroke="#f7941d" stroke-width="2.4" fill="none"/></svg>Disaster Recovery</li>
    <li><svg width="12" height="12" viewBox="0 0 12 12"><path d="M1 6l3 3 7-7" stroke="#f7941d" stroke-width="2.4" fill="none"/></svg>Corporate or Satellite Offices</li>
    <li><svg width="12" height="12" viewBox="0 0 12 12"><path d="M1 6l3 3 7-7" stroke="#f7941d" stroke-width="2.4" fill="none"/></svg>All-Inclusive Pricing!</li>
  </ul>
  <span class="btn btn-orange-on-navy"><span class="dot"></span>Read More »</span>
</section>

<section class="offer offer-right abs">
  <div class="offer-icon abs"><div class="icon-fill" role="img" aria-label="Person working at a computer icon"></div></div>
  <h2>VIRTUAL OFFICE</h2>
  <ul>
    <li><svg width="12" height="12" viewBox="0 0 12 12"><path d="M1 6l3 3 7-7" stroke="#27366b" stroke-width="2.4" fill="none"/></svg>Mailing Address $49/mo</li>
    <li><svg width="12" height="12" viewBox="0 0 12 12"><path d="M1 6l3 3 7-7" stroke="#27366b" stroke-width="2.4" fill="none"/></svg>Flexible Contracts</li>
    <li><svg width="12" height="12" viewBox="0 0 12 12"><path d="M1 6l3 3 7-7" stroke="#27366b" stroke-width="2.4" fill="none"/></svg>Local Phone &amp; Mail $99/mo</li>
    <li><svg width="12" height="12" viewBox="0 0 12 12"><path d="M1 6l3 3 7-7" stroke="#27366b" stroke-width="2.4" fill="none"/></svg>All-Inclusive Pricing!</li>
    <li><svg width="12" height="12" viewBox="0 0 12 12"><path d="M1 6l3 3 7-7" stroke="#27366b" stroke-width="2.4" fill="none"/></svg>Corporate or Satellite Offices</li>
  </ul>
  <span class="btn btn-navy"><span class="dot" style="background:#fff"></span>Read More »</span>
</section>
<div class="notch abs"></div>
<div class="link-line abs"></div>
<div class="center-seal abs"></div>

<section class="community abs">
  <h2 class="block-title" style="font-weight:400">COMMUNITY</h2>
  <div class="community-photo" role="img" aria-label="Photo of many hands stacked together in a team huddle"></div>
  <p>Lorem ipsum dolor sit amet, consectetuer adipiscing elit, sed diam nonummy nibh euismod tincidunt ut laoreet dolore magna aliquam erat volutpat. Ut wisi enim ad minim veniam, quis nostrud exerci tation ullamcorper suscipit lobortis nisl ut aliquip ex ea commodo consequat. Duis autem vel eum iriure dolor in hendrerit in vulputate velit esse molestie consequat, vel illum dolore eu feugiat nulla facilisis at vero eros et accumsan et iusto odio dignissim qui blandit</p>
  <span class="read-link">Read More »</span>
</section>

<section class="services abs">
  <h2 class="block-title" style="font-weight:400">OTHER SERVICES</h2>
  <div class="rule-top"></div>
  <div class="svc" style="top:110px"><span class="svc-icon"></span><h3>On-demand Meeting Rooms</h3><p>Lorem ipsum dolor sit amet, consectetuer adipiscing elit, sed diam my nibh euismod dloer sknev cjsrewvc bnarv bdivrt.</p><span class="read-link">Read More »</span></div>
  <div class="svc" style="top:246px"><span class="svc-icon"></span><h3>On-demand Training Rooms</h3><p>Lorem ipsum dolor sit amet, consectetuer adipiscing elit, sed diam my nibh euismod dloer sknev cjsrewvc bnarv bdivrt.</p><span class="read-link">Read More »</span></div>
  <div class="svc" style="top:382px;border-bottom:none"><span class="svc-icon"></span><h3>Virtual Office Solutions</h3><p>Lorem ipsum dolor sit amet, consectetuer adipiscing elit, sed diam my nibh euismod dloer sknev cjsrewvc bnarv bdivrt.</p><span class="read-link">Read More »</span></div>
</section>

<section class="partners abs">
  <h2 class="sec-title" style="font-weight:400">OUR PARTNERS</h2>
  <div class="divider"><i></i><b></b><i></i></div>
  <svg class="p-arrow abs" style="left:14px" width="22" height="46" viewBox="0 0 22 46"><path d="M20 2L3 23l17 21" stroke="#bbb" stroke-width="2" fill="none"/></svg>
  <div class="partner-row">
    <div class="partner"><span></span></div><div class="partner"><span></span></div><div class="partner"><span></span></div>
    <div class="partner"><span></span></div><div class="partner"><span></span></div><div class="partner"><span></span></div>
  </div>
  <svg class="p-arrow abs" style="left:1164px" width="22" height="46" viewBox="0 0 22 46"><path d="M2 2l17 21L2 44" stroke="#bbb" stroke-width="2" fill="none"/></svg>
</section>

<svg class="footer-curve abs" width="1200" height="62" viewBox="0 0 1200 62"><path d="M0 62 Q600 -40 1200 62 Z" fill="#1f2d5c" stroke="#c9ccd4" stroke-width="4"/><rect x="0" y="58" width="1200" height="4" fill="#1f2d5c"/></svg>
<div class="footer-seal abs"></div>

<footer class="footer abs">
  <div class="f-col" style="left:60px;width:190px">
    <h4>QUICK LINKS</h4>
    <ul class="f-links"><li>Home</li><li>Properties</li><li>Virtual Tours &amp; Videos</li><li>Photos</li><li>Broker Referrals</li></ul>
  </div>
  <div class="f-col" style="left:310px;width:240px">
    <h4>CONTACT DETAILS</h4>
    <div class="contact-row"><svg width="12" height="16" viewBox="0 0 12 16"><path d="M6 0a6 6 0 0 1 6 6c0 4-6 10-6 10S0 10 0 6a6 6 0 0 1 6-6z" fill="#f7941d"/><circle cx="6" cy="6" r="2" fill="#1f2d5c"/></svg><div><b>CALLOWAY BUSINESS CENTERS</b><br>4120 Harlan Parkway<br>Suite 300 , Dallas, Texas 75204</div></div>
    <div class="contact-row"><svg width="13" height="13" viewBox="0 0 24 24"><path d="M5 2l4 0 2 5-3 2a11 11 0 0 0 7 7l2-3 5 2 0 4a3 3 0 0 1-3 3A19 19 0 0 1 2 5a3 3 0 0 1 3-3z" fill="#f7941d"/></svg>+ 214.555.0148</div>
    <div class="contact-row"><svg width="14" height="13" viewBox="0 0 14 13"><rect x="3" y="0" width="8" height="4" fill="#f7941d"/><rect x="0" y="4" width="14" height="6" rx="1" fill="#f7941d"/><rect x="3" y="8" width="8" height="5" fill="#fff"/></svg>+ 214.555.0149</div>
    <div class="contact-row"><svg width="14" height="11" viewBox="0 0 14 11"><rect width="14" height="11" rx="1" fill="#f7941d"/><path d="M0 1l7 5 7-5" stroke="#1f2d5c" fill="none"/></svg>Offices@CallowayOffices.com</div>
  </div>
  <div class="f-col" style="left:644px;width:276px">
    <h4>QUICK CONTACT</h4>
    <div class="field">Name</div><div class="field">Email</div><div class="field">Message</div>
    <div class="submit">Submit</div>
  </div>
  <div class="f-col" style="left:1018px;width:130px">
    <h4>FOLLOW US</h4>
    <ul class="follow">
      <li><span style="background:#dd4b39"></span>PLUSLINE</li>
      <li><span style="background:#1da1f2"></span>CHIRPER</li>
      <li><span style="background:#0e76a8"></span>LINKFOLD</li>
      <li><span style="background:#d2232a"></span>PINBOARD</li>
    </ul>
  </div>
</footer>
<div class="v-rule abs" style="left:280px"></div>
<div class="v-rule abs" style="left:600px"></div>
<div class="v-rule abs" style="left:966px"></div>

<div class="copyright abs">Copyright © 2016 &nbsp;Calloway Business Centers. All Rights Reserved.</div>

</body>
</html>
```